Business card design for Talvren Engineering Tandem

We need a new business card design along with all the necessary to place an order. The company is Talvren Engineering Tandem and we recently updated our logo.

```html
<!DOCTYPE html>
<html lang="en">
<head>
<meta charset="utf-8">
<title>Talvren Engineering Tandem – Business Card</title>
<link rel="stylesheet" href="https://fonts.googleapis.com/css2?family=Nunito+Sans:wght@400;700;800&display=swap">
<style>
  :root {
    --stage: #1b1b1f;
    --card: #24272a;
    --brand-grey: #a3a3a3;
    --text-grey: #b9b9b9;
    --accent: #f2c91f;
  }
  * { margin: 0; padding: 0; box-sizing: border-box; }
  html, body {
    width: 1200px; height: 800px; overflow: hidden;
    background: var(--stage);
    font-family: "Nunito Sans", sans-serif;
  }
  .canvas {
    width: 1200px; height: 800px;
    display: flex; align-items: center; justify-content: center; gap: 40px;
  }
  .card {
    position: relative;
    width: 540px; height: 310px;
    background: var(--card);
    border-radius: 22px;
    overflow: hidden;
    box-shadow: 0 18px 40px rgba(0,0,0,.45);
  }
  .wordmark {
    position: absolute;
    display: flex; align-items: center; gap: 12px;
    color: var(--brand-grey);
    font-weight: 800;
    letter-spacing: .04em;
    line-height: 1;
    white-space: nowrap;
  }
  .wordmark-square { width: 14px; height: 14px; background: var(--accent); flex: none; }
  .wordmark-name { text-transform: uppercase; }
  .card-front .wordmark {
    left: 50%; top: 50%; transform: translate(-50%, -50%);
    font-size: 24px;
  }
  .card-back .wordmark {
    left: 36px; top: 44px;
    font-size: 22px;
  }
  .contact {
    position: absolute; left: 36px; bottom: 28px;
    color: var(--text-grey);
    font-size: 14px; line-height: 1.45;
  }
  .person-name {
    font-weight: 700; font-size: 17px; letter-spacing: .03em;
    text-transform: uppercase;
  }
  .person-role { color: var(--accent); font-size: 15px; margin-bottom: 10px; }
  .address { margin-bottom: 10px; }
  .contact-line { display: flex; align-items: center; gap: 8px; }
  .contact-line svg { width: 13px; height: 13px; flex: none; }
</style>
</head>
<body>
  <main class="canvas">
    <section class="card card-front">
      <div class="wordmark">
        <span class="wordmark-square"></span>
        <span class="wordmark-name">Talvren Engineering Tandem</span>
      </div>
    </section>

    <section class="card card-back">
      <div class="wordmark">
        <span class="wordmark-square"></span>
        <span class="wordmark-name">Talvren Engineering Tandem</span>
      </div>
      <div class="contact">
        <p class="person-name">Daren K. Holt</p>
        <p class="person-role">Partner</p>
        <p class="address">Level 3, 48 Kestrel Road<br>Marlow NSW 2091</p>
        <p class="contact-line">
          <svg viewBox="0 0 16 16"><rect x="4" y="1.5" width="8" height="13" rx="1.5" fill="none" stroke="var(--accent)" stroke-width="1.6"/><circle cx="8" cy="12" r="0.9" fill="var(--accent)"/></svg>
          0198 765 432
        </p>
        <p class="contact-line">
          <svg viewBox="0 0 16 16"><rect x="1.5" y="3.5" width="13" height="9" fill="var(--accent)"/><path d="M1.5 3.5 8 9l6.5-5.5" fill="none" stroke="var(--card)" stroke-width="1.2"/></svg>
          info@talvrentandem.co
        </p>
        <p class="contact-line">
          <svg viewBox="0 0 16 16"><circle cx="8" cy="8" r="6.5" fill="none" stroke="var(--accent)" stroke-width="1.4"/><ellipse cx="8" cy="8" rx="2.8" ry="6.5" fill="none" stroke="var(--accent)" stroke-width="1.1"/><path d="M1.5 8h13" stroke="var(--accent)" stroke-width="1.1"/></svg>
          www.talvrentandem.co
        </p>
      </div>
    </section>
  </main>
</body>
</html>
```